Christmas Collection Candle Label Design

Looking to update our existing Christmas Candle Collection labels. Labels should reflect the overall feel of our brand- www.kelvanoro.ca
Want to include some color elements. Holiday colors added into design but more muted/ earthy tones not vibrant colors . Metallic elements and line art botanical illustration. Fonts should be more align to brand
Scents
Holiday Tree
Candy Cane
Sugar and Spice
Joyeaux Noel

```html
<!DOCTYPE html>
<html lang="en">
<head>
<meta charset="utf-8">
<title>Kelvanoro – Holiday Tree Candle Label</title>
<link rel="stylesheet" href="https://fonts.googleapis.com/css2?family=Libre+Baskerville:wght@400;700&family=Open+Sans:wght@400;600&display=swap">
<style>
  :root {
    --backdrop: #bca48b;
    --label-dark: #6e5640;
    --label-mid: #86694d;
    --label-light: #a98c6c;
    --ink: #ece0d0;
    --ink-soft: #d9c8b2;
    --gold-light: #c9ab80;
    --gold-deep: #a3845f;
  }
  * { margin: 0; padding: 0; box-sizing: border-box; }
  html, body {
    width: 1200px;
    height: 1157px;
    overflow: hidden;
    background: var(--backdrop);
  }
  .canvas {
    position: relative;
    width: 1200px;
    height: 1157px;
  }
  .label {
    position: absolute;
    left: 100px;
    top: 265px;
    width: 1000px;
    height: 628px;
    background: linear-gradient(90deg, var(--label-light) 0%, var(--label-mid) 30%, var(--label-dark) 55%, var(--label-mid) 80%, var(--label-light) 100%);
    color: var(--ink);
  }
  .brand {
    position: absolute;
    top: 62px;
    left: 0;
    width: 100%;
    text-align: center;
  }
  .brand-name {
    font-family: "Libre Baskerville", serif;
    font-size: 28px;
    font-weight: 400;
    letter-spacing: 1px;
    color: var(--ink);
  }
  .brand-tagline {
    margin-top: 4px;
    font-family: "Open Sans", sans-serif;
    font-size: 9px;
    letter-spacing: 2px;
    color: var(--ink-soft);
  }
  .rule {
    position: absolute;
    height: 3px;
    background: var(--ink);
  }
  .rule-top { top: 150px; left: 120px; width: 760px; }
  .rule-bottom-upper { top: 524px; left: 120px; width: 748px; }
  .rule-bottom-lower { top: 588px; left: 120px; width: 748px; }
  .scent-name {
    position: absolute;
    top: 188px;
    left: 120px;
    font-family: "Libre Baskerville", serif;
    font-weight: 700;
    font-size: 83px;
    line-height: 100px;
    letter-spacing: 1px;
    color: var(--ink);
  }
  .scent-note {
    position: absolute;
    top: 395px;
    left: 120px;
    font-family: "Open Sans", sans-serif;
    font-size: 21px;
    color: var(--ink);
  }
  .botanical-art {
    position: absolute;
    top: 180px;
    left: 600px;
    width: 335px;
    height: 290px;
  }
  .details {
    position: absolute;
    top: 544px;
    left: 120px;
    width: 748px;
    display: flex;
    justify-content: space-between;
    font-family: "Open Sans", sans-serif;
    font-size: 23px;
    color: var(--ink);
  }
</style>
</head>
<body>
<div class="canvas">
  <div class="label">
    <div class="brand">
      <div class="brand-name">KELVANORO</div>
      <div class="brand-tagline">PURE PLANT BASED SCENTS</div>
    </div>
    <div class="rule rule-top"></div>
    <h1 class="scent-name">HOLIDAY<br>TREE</h1>
    <p class="scent-note">MADE WITH PLANT BASED BOTANICAL</p>
    <svg class="botanical-art" role="img" aria-label="Metallic gold line art botanical illustration of lily flowers and buds" viewBox="0 0 335 290">
      <defs>
        <linearGradient id="artGold" x1="0" y1="0" x2="1" y2="1">
          <stop offset="0%" stop-color="#c9ab80"/>
          <stop offset="100%" stop-color="#a3845f"/>
        </linearGradient>
      </defs>
      <rect width="335" height="290" rx="14" fill="url(#artGold)" opacity="0.75"/>
    </svg>
    <div class="rule rule-bottom-upper"></div>
    <div class="details">
      <span>13 OZ</span>
      <span>//</span>
      <span>MADE IN CANADA</span>
    </div>
    <div class="rule rule-bottom-lower"></div>
  </div>
</div>
</body>
</html>
```